Evaporative Air Conditioning Summer Service

Would like to design a flyer to send out in an email to existing clients to promote a Pre-summer service for Evaporative Air Conditioners
Cost will be $110.00 inc gst
Tasks included in service are
- Inspection and clean of pads
- Inspection and check float valve, water pump, fan, motor, bearings, drain
- Clean basin
- Supply of bacterial tablet
- Inspect overall condition of unit
- Any repairs if required will be quoted
Please see files attached of a previous very basic flyer I have used for installation and replacement unit costs. This has current contact information
Have also uploaded company logo for use.
Thanks
Plumbing

```html
<!DOCTYPE html>
<html lang="en">
<head>
<meta charset="utf-8">
<title>Summit Gas &amp; Plumbing – Evaporative Summer Service</title>
<link rel="stylesheet" href="https://fonts.googleapis.com/css2?family=Poppins:wght@500;600;700&display=swap">
<style>
  :root {
    --blue: #1877b7;
    --blue-light: #5f9fd3;
    --orange: #e0602c;
    --paper: #f4f4f4;
    --backdrop: #e4e4e4;
    --white: #ffffff;
    --photo-a: #b9c0c7;
    --photo-b: #8c6f52;
  }
  * { margin: 0; padding: 0; box-sizing: border-box; }
  html, body { width: 1200px; height: 1006px; overflow: hidden; }
  body {
    background: var(--backdrop);
    font-family: "Poppins", sans-serif;
    position: relative;
  }
  .flyer {
    position: absolute;
    left: 257px; top: 23px;
    width: 686px; height: 960px;
    background: var(--paper);
    overflow: hidden;
  }
  .hero-art { position: absolute; left: 0; top: 0; }
  .brand {
    position: absolute;
    left: 318px; top: 58px;
    display: flex; align-items: center; gap: 12px;
  }
  .brand-dot {
    width: 34px; height: 34px; border-radius: 50%;
    background: var(--orange);
  }
  .brand-name {
    color: var(--blue);
    font-weight: 700;
    font-size: 25px;
    line-height: 1;
    letter-spacing: 0.5px;
  }
  .price-badge {
    position: absolute;
    left: 50px; top: 222px;
    width: 192px; height: 192px;
    border-radius: 50%;
    background: var(--orange);
    box-shadow: 0 0 0 4px var(--paper), 0 0 0 8px var(--blue-light);
    color: var(--white);
    display: flex; flex-direction: column; align-items: center; justify-content: center;
    text-align: center;
  }
  .price-amount { font-weight: 700; font-size: 44px; line-height: 1; }
  .price-note { font-weight: 600; font-size: 23px; line-height: 1.2; margin-top: 4px; }
  .photo {
    position: absolute;
    border-radius: 14px;
  }
  .photo-pads { left: 23px; top: 426px; width: 200px; height: 138px;
    background: linear-gradient(135deg, #dfe3e7, #b97a4f); }
  .photo-valve { left: 243px; top: 426px; width: 200px; height: 138px;
    background: linear-gradient(135deg, #bdb8b2, #e8e8ea); }
  .photo-technician { left: 464px; top: 574px; width: 211px; height: 145px;
    background: linear-gradient(135deg, #c8ccce, #7ea3c8); }
  .offer-box {
    position: absolute;
    left: 464px; top: 400px; width: 222px; height: 158px;
    background: var(--orange);
    border-top-left-radius: 34px;
    border-bottom-left-radius: 34px;
    color: var(--white);
    text-align: right;
    padding: 14px 18px 0 0;
    font-weight: 600; font-size: 24.5px; line-height: 32px;
  }
  .services {
    position: absolute;
    left: 0; top: 583px; width: 443px; height: 377px;
    background: var(--blue);
    border-top-right-radius: 48px;
  }
  .services-tag {
    position: absolute;
    left: 19px; top: 574px;
    height: 34px; padding: 0 16px;
    background: var(--orange);
    border-radius: 17px;
    color: var(--white);
    font-weight: 600; font-size: 25px; line-height: 35px;
  }
  .service-list {
    position: absolute;
    left: 22px; top: 624px; width: 420px;
    list-style: none;
    color: var(--white);
    font-weight: 500; font-size: 18px; line-height: 36px;
  }
  .service-list li {
    position: relative;
    padding-left: 32px;
    margin-bottom: 1px;
  }
  .service-list li::before {
    content: "";
    position: absolute; left: 3px; top: 12px;
    width: 13px; height: 13px; border-radius: 50%;
    background: var(--orange);
  }
  .service-list li.two-line { line-height: 36px; }
  .contact-email {
    position: absolute;
    left: 21px; top: 890px; width: 409px; height: 44px;
    background: var(--orange);
    border-radius: 10px;
    color: var(--white);
    font-weight: 500; font-size: 16.5px; line-height: 44px;
    text-align: center;
  }
  .rates-box {
    position: absolute;
    left: 464px; top: 736px; width: 222px; height: 224px;
    background: var(--blue);
    border-top-left-radius: 34px;
    color: var(--white);
    text-align: right;
    padding: 12px 18px 0 0;
    font-weight: 600; font-size: 23.5px; line-height: 31.5px;
  }
  .contact-phone {
    position: absolute;
    left: 484px; top: 890px; width: 202px; height: 46px;
    background: var(--orange);
    border-radius: 10px 0 0 10px;
    color: var(--white);
    font-weight: 700; font-size: 28px; line-height: 46px;
    text-align: center;
  }
</style>
</head>
<body>
  <main class="flyer">
    <svg class="hero-art" width="686" height="410" viewBox="0 0 686 410" aria-hidden="false">
      <defs>
        <linearGradient id="house-tones" x1="0" y1="0" x2="1" y2="1">
          <stop offset="0" stop-color="#c9ced3"/>
          <stop offset="0.6" stop-color="#a9aeb3"/>
          <stop offset="1" stop-color="#b88a5a"/>
        </linearGradient>
        <linearGradient id="cooler-tones" x1="0" y1="0" x2="0" y2="1">
          <stop offset="0" stop-color="#3a3c40"/>
          <stop offset="1" stop-color="#9ea3a8"/>
        </linearGradient>
      </defs>
      <path class="swoosh" d="M0 148 C50 260 170 360 300 392 L300 404 C160 382 40 300 0 236 Z" fill="var(--blue)"/>
      <g role="img" aria-label="Evaporative cooler unit on the roof of a modern two-storey house">
        <path d="M14 150 L686 150 L686 352 C600 388 480 400 380 396 C210 388 90 290 14 150 Z" fill="url(#house-tones)"/>
        <rect x="44" y="19" width="196" height="176" rx="14" fill="url(#cooler-tones)"/>
      </g>
      <path class="accent-curve" d="M464 404 C560 394 630 376 686 350 L686 404 Z" fill="var(--orange)"/>
    </svg>

    <div class="brand">
      <span class="brand-dot"></span>
      <span class="brand-name">Summit Gas &amp; Plumbing</span>
    </div>

    <div class="price-badge">
      <span class="price-amount">$110.00</span>
      <span class="price-note">INC GST</span>
    </div>

    <div class="photo photo-pads" role="img" aria-label="Technician cleaning an evaporative cooler pad with a hose"></div>
    <div class="photo photo-valve" role="img" aria-label="Float valve and water pipe fittings inside a cooler basin"></div>

    <div class="offer-box">AIR CON<br>REPAIR<br>SUPPLY AND<br>INSTALLATION</div>

    <section class="services">
    </section>
    <div class="services-tag">SERVICE ARE</div>
    <ul class="service-list">
      <li>Inspection and clean of pads</li>
      <li class="two-line">Inspection and check float valve,<br>water pump, fan, motor, bearings, drain</li>
      <li>Clean basin</li>
      <li style="margin-top:6px">Supply of bacterial tablet</li>
      <li>Inspect overall condition of unit</li>
      <li>Any repairs if required will be quoted</li>
    </ul>
    <div class="contact-email">admin@summitgasplumbing.com.au</div>

    <div class="photo photo-technician" role="img" aria-label="Technician repairing the wiring of an outdoor air conditioning unit"></div>

    <div class="rates-box">FAULT FINDING<br>AND REPAIRS<br>AS PER NORMAL<br>HOURLY RATE</div>
    <div class="contact-phone">040 5521 837</div>
  </main>
</body>
</html>
```